Business Card Design for company

We want new business cards. We'd like something different-- yet still highly professional. Our tagline is Guiding strategy, building results. Stock photos are ok, as long as they are relevant and look upscale.

Target Market(s)

Architecture/Business Management Consulting/Engineering Consulting

Contact Information for Business Card

dark gray background with pops of blue might be good, but you tell me. You're the designers. Rounded corners might be nice, but again, you tell me.

Font styles to use
Serif
Sans Serif

Colors
3276b5
5c5c5c
9d9d9d
fbfbfb

Requirements
Nice to have
• Something different, but still very professional.

```html
<!DOCTYPE html>
<html lang="en">
<head>
<meta charset="utf-8">
<title>Verold Partners – Business Card</title>
<link rel="stylesheet" href="https://fonts.googleapis.com/css2?family=Montserrat:wght@400;600;700&family=Open+Sans:wght@400;600&display=swap">
<style>
  :root {
    --bg: #2b2b2d;
    --blue: #3276b5;
    --blue-deep: #2a5f98;
    --blue-light: #4ab0ee;
    --ink: #5c5c5c;
    --ink-soft: #9d9d9d;
    --paper: #fbfbfb;
  }
  * { box-sizing: border-box; margin: 0; padding: 0; }
  html, body { width: 1200px; height: 885px; overflow: hidden; background: var(--bg); }
  .canvas {
    width: 1200px; height: 885px;
    display: flex; flex-direction: column; align-items: center; justify-content: center;
    gap: 29px;
  }
  .card { width: 700px; height: 400px; position: relative; overflow: hidden; }

  /* Front */
  .card-front {
    background: linear-gradient(135deg, var(--blue-light) 0%, var(--blue) 45%, var(--blue-deep) 100%);
    color: var(--paper);
  }
  .front-wordmark {
    position: absolute; left: 0; right: 0; top: 130px; text-align: center;
    font-family: "Montserrat", sans-serif; font-weight: 600; font-size: 84px; letter-spacing: 4px;
    white-space: nowrap;
  }
  .front-tagline {
    position: absolute; left: 0; right: 0; top: 300px; text-align: center;
    font-family: "Open Sans", sans-serif; font-size: 17px; letter-spacing: 0.3px;
    white-space: nowrap;
  }
  .front-tagline .dot { display: inline-block; width: 7px; height: 7px; border-radius: 50%; background: var(--paper); margin: 0 9px; vertical-align: middle; }

  /* Back */
  .card-back { background: var(--paper); font-family: "Open Sans", sans-serif; color: var(--ink); }
  .name-band {
    position: absolute; left: 0; top: 118px; width: 380px; height: 66px;
    background: var(--blue); color: var(--paper); padding: 12px 0 0 70px;
    white-space: nowrap;
  }
  .band-rule { position: absolute; top: 118px; width: 3px; height: 66px; background: var(--blue); }
  .band-rule.one { left: 388px; }
  .band-rule.two { left: 396px; background: var(--ink); }
  .person-name { font-family: "Montserrat", sans-serif; font-weight: 700; font-size: 21px; line-height: 1.1; letter-spacing: 0.5px; }
  .person-title { font-size: 14px; letter-spacing: 0.5px; }
  .brand-name {
    position: absolute; left: 412px; top: 136px; display: flex; align-items: center; gap: 10px;
    font-family: "Montserrat", sans-serif; font-weight: 600; font-size: 25px; color: var(--ink); line-height: 1;
    white-space: nowrap;
  }
  .brand-name .mark { width: 13px; height: 13px; background: var(--blue); flex: none; }
  .address {
    position: absolute; right: 42px; top: 226px; text-align: right; font-size: 14.5px; line-height: 1.45;
    font-style: normal; white-space: nowrap;
  }
  .contacts { position: absolute; left: 210px; top: 298px; font-size: 15px; line-height: 1.55; list-style: none; white-space: nowrap; }
  .contacts li { display: flex; align-items: center; gap: 12px; }
  .contacts svg { width: 16px; height: 16px; fill: var(--blue); flex: none; }
</style>
</head>
<body>
<main class="canvas">
  <section class="card card-front" aria-label="Card front">
    <div class="front-wordmark">Verold</div>
    <p class="front-tagline">Guiding strategy<span class="dot"></span>building results</p>
  </section>

  <section class="card card-back" aria-label="Card back">
    <div class="name-band">
      <div class="person-name">EVAN MARLOW</div>
      <div class="person-title">PRESIDENT</div>
    </div>
    <span class="band-rule one"></span>
    <span class="band-rule two"></span>
    <div class="brand-name"><span class="mark"></span>Verold Partners</div>

    <address class="address">
      2170 Halden Court<br>
      Brookfield, NY 10099<br>
      www.veroldpartners.com
    </address>

    <ul class="contacts">
      <li>
        <svg viewBox="0 0 16 16" aria-hidden="true"><path d="M2 5c0-2 2-3 6-3s6 1 6 3v1h-3V5H5v1H2z"/><rect x="3" y="7" width="10" height="7" rx="1.5"/></svg>
        555 0142 7781
      </li>
      <li>
        <svg viewBox="0 0 16 16" aria-hidden="true"><path d="M4 1h8v14H4zM5.5 2.5v9h5v-9z"/></svg>
        555 0198 3306
      </li>
      <li>
        <svg viewBox="0 0 16 16" aria-hidden="true"><path d="M1 4h14v9H1zM2.5 5.2v.6L8 9.3l5.5-3.5v-.6z"/></svg>
        evan@veroldpartners.com
      </li>
    </ul>
  </section>
</main>
</body>
</html>
```